Moxy Fen needs some awesome stationary

Do you have what it takes to get my brand? You either do or you don't, have a crack at a design and you my just win my business.

I don't want to waste your or my time, so put your creative genius on either a business card or envelope.

I however need a package of stationary that follows the same brand. I will message you to complete the remaining should I like your first submission.

Here is what I need, have a go!

Basically I need the following for my small business based in melbourne.
- Letterhead (printer ready and MS Word)
- Business Card
- Compliments Slip
- Envelope
- Proposal Cover Page (MS Word only)
- Presentation Folder
- Marbled Fox Cards
- Student Name Tent
- Index Cards
- Vell-Ka

I am establishing the brand and it must be modern, professional but also relaxed; that is not formal and not corporate. It represents a company are leaders, but small enough to care and operate like a bunch of friends. We are bringing people and conversations back to business, and turfing out all the bureaucracy and crazy and wasteful procedures. Its about "lets talk and figure it out together and find even better ways".

Target Market(s)

Mainly companies that build software products, but Agile practices are used in many other industries (even graphic design projects)

Industry/Entity Type

Information Technology

Font styles to use
Sans Serif

Colors
3176b5
aaaaaa

Requirements
Must have
• I like curves and circles and not boxes or rectangles.
• I want a colour rich design with my brand colours, but it must be balanced.
• I want more modern than traditional, but simple modern
Should not have
• Not corporate
• Please don't waste my time if your not going to think about it.
• Don't mess with my primary logo
• Don't change my colours
• Don't overlay logo on image

```html
<!DOCTYPE html>
<html lang="en">
<head>
<meta charset="utf-8">
<title>Moxy Fen — Business Card</title>
<link rel="stylesheet" href="https://fonts.googleapis.com/css2?family=Open+Sans:wght@400;600;700&display=swap">
<style>
  :root {
    --brand-blue: #2b5ca4;
    --brand-grey: #98a0ac;
    --text-grey: #7d8590;
    --text-dark: #4a4f56;
    --card-white: #ffffff;
    --backdrop: #6a4a36;
    --divider: #d6d9de;
  }
  * { margin: 0; padding: 0; box-sizing: border-box; }
  html, body { width: 1200px; height: 987px; overflow: hidden; }
  body {
    background: var(--backdrop);
    font-family: "Open Sans", sans-serif;
    position: relative;
  }
  .card {
    position: absolute;
    left: 293px;
    width: 615px;
    height: 350px;
    border-radius: 16px;
    overflow: hidden;
  }
  .card--front { top: 131px; background: var(--card-white); }
  .card--back { top: 506px; background: var(--brand-grey); }

  .brand-lockup {
    position: absolute;
    left: 40px;
    top: 86px;
    width: 256px;
    text-align: center;
  }
  .brand-lockup__dot {
    display: block;
    width: 104px;
    height: 104px;
    margin: 0 auto 12px;
    border-radius: 50%;
    background: var(--brand-blue);
  }
  .brand-lockup__name {
    font-size: 40px;
    font-weight: 700;
    color: var(--brand-blue);
    line-height: 1;
    letter-spacing: 0.2px;
  }
  .divider {
    position: absolute;
    left: 291px;
    top: 60px;
    width: 1px;
    height: 236px;
    background: var(--divider);
  }
  .contact {
    position: absolute;
    left: 314px;
    top: 62px;
    color: var(--text-dark);
  }
  .contact__name {
    font-size: 22px;
    font-weight: 600;
    color: var(--brand-blue);
    line-height: 1.2;
  }
  .contact__role {
    font-size: 16px;
    color: var(--text-grey);
    line-height: 1.3;
  }
  .contact__address {
    margin-top: 14px;
    font-size: 16px;
    line-height: 22px;
    font-style: normal;
  }
  .contact__list {
    list-style: none;
    margin-top: 9px;
    font-size: 16px;
    line-height: 23.5px;
  }
  .contact__list li { display: flex; align-items: center; gap: 8px; }
  .contact__list svg { width: 14px; height: 14px; fill: var(--brand-blue); flex: none; }

  .band {
    position: absolute;
    left: 0;
    bottom: 0;
    width: 100%;
    height: 23px;
  }

  .back-wordmark {
    position: absolute;
    left: 30px;
    bottom: 30px;
    transform-origin: left bottom;
    transform: rotate(-90deg) translateY(100%);
    white-space: nowrap;
    color: var(--card-white);
  }
  .back-wordmark__name {
    display: block;
    font-size: 50px;
    font-weight: 700;
    line-height: 1;
  }
  .back-wordmark__url {
    display: block;
    font-size: 15px;
    letter-spacing: 4.2px;
    margin-top: 8px;
  }
  .back-disc {
    position: absolute;
    left: 148px;
    top: 8px;
    width: 334px;
    height: 334px;
    border-radius: 50%;
    background: var(--brand-blue);
  }
</style>
</head>
<body>

<section class="card card--front" aria-label="Business card front">
  <div class="brand-lockup">
    <span class="brand-lockup__dot" aria-hidden="true"></span>
    <div class="brand-lockup__name">Moxy Fen</div>
  </div>

  <div class="divider"></div>

  <div class="contact">
    <div class="contact__name">Dana Quell</div>
    <div class="contact__role">CEO, Certified Agile Trainer</div>
    <address class="contact__address">
      PO Box 4418<br>
      Birchwood Vale<br>
      VIC 3199, Australia
    </address>
    <ul class="contact__list">
      <li>
        <svg viewBox="0 0 16 16" aria-hidden="true"><path d="M3.6 1.2l2.3 2.6c.4.4.4 1 0 1.4L4.8 6.4c.9 2 2.6 3.8 4.8 4.8l1.2-1.1c.4-.4 1-.4 1.4 0l2.6 2.3c.4.4.4 1 0 1.4l-1.4 1.3C10.2 15.8 .2 5.8 2.2 2.6l1.4-1.4z"/></svg>
        1300MOXYF
      </li>
      <li>
        <svg viewBox="0 0 16 16" aria-hidden="true"><path d="M4.5 0h7c.8 0 1.5.7 1.5 1.5v13c0 .8-.7 1.5-1.5 1.5h-7C3.7 16 3 15.3 3 14.5v-13C3 .7 3.7 0 4.5 0zM4.8 2v10.5h6.4V2H4.8zM8 13.3a.9.9 0 100 1.8.9.9 0 000-1.8z"/></svg>
        +61 400 555 017
      </li>
      <li>
        <svg viewBox="0 0 16 16" aria-hidden="true"><path d="M1 3h14v1.2L8 8.6 1 4.2V3zm0 2.8l7 4.4 7-4.4V13H1V5.8z"/></svg>
        dana@moxy-fen.com.au
      </li>
      <li>
        <svg viewBox="0 0 16 16" aria-hidden="true"><circle cx="8" cy="8" r="7.5"/><path d="M5 4c1.5.5 2 1.5 1.2 2.6C5.6 7.6 4 7.5 4.5 9.5 5 11 6 11 6 13M10 2.5c-.5 1.5.5 2.5 2 2.5s2 1.5 1 3-2.5 1-3 2.5.5 2.5 0 3.5" stroke="#fff" stroke-width="1.2" fill="none"/></svg>
        www.moxy-fen.com.au
      </li>
    </ul>
  </div>

  <svg class="band" viewBox="0 0 615 23" preserveAspectRatio="none" aria-hidden="true">
    <polygon points="0,0 395,0 389,23 0,23" fill="var(--brand-blue)"/>
    <polygon points="399,0 615,0 615,23 393,23" fill="var(--brand-grey)"/>
  </svg>
</section>

<section class="card card--back" aria-label="Business card back">
  <div class="back-wordmark">
    <span class="back-wordmark__name">Moxy Fen</span>
    <span class="back-wordmark__url">www.moxy-fen.com.au</span>
  </div>
  <span class="back-disc" aria-hidden="true"></span>
</section>

</body>
</html>
```